Popup Nightclub Grand Opening Flyer

We need to design a flyer for the grand opening of an upscale, exclusive nightclub called "Lantern". The design needs to be chic and exclusive. The background should be black and the text should primarily be white. We like minimalist designs.

Here is the text for the flyer
-
Velvetroll Atlanta Presents

Lantern (LOGO)

A Popup Nightclub Experience
For one night Only

Friday, October 18, 2013
Party begins at 9PM

INVITE ONLY

See invitation for location details
(Velvetroll Atlanta logo)

-
Examples we like

http://cdn4-x.pressfolio-example.com/sites/default/files/styles/image_content_width/hash/3b/fd/2468013579_4421_flyer.jpg?itok=K9rtQw2z

http://files.hubspace-example.net/files/8Hqq-Tr72WWE3kaRbTmcxP5QZK2F396J8nbRw4CKMHfdX2Y7qSEF-MqjxDoNrLY3QCyQJD7npjGaRq3k-Mhx6hqf3MDSWf8r3/2zenSaturdays.jpg

http://morvex-example.com/wp-content/uploads/siteskin/widgetkit/gallery/2zen/2zen-gen_qstay4-01.jpg

Hi All, one thing that we are seeing that we don't like is on over emphasis on the phrase "a popup nightclub experience" please don't make this the largest thing on the flyer

Target Market(s)

Target market is 25-35 year olds who are affluent (rich) and like luxury brands

Requirements
Must have
• Dark Background
Nice to have
• Velvetroll Logo on the bottom
Modern text that isn't curvy
Should not have
• Curved text

```html
<!DOCTYPE html>
<html lang="en">
<head>
<meta charset="utf-8">
<title>Lantern Nightclub – Velvetroll Atlanta</title>
<link rel="stylesheet" href="https://fonts.googleapis.com/css2?family=Raleway:wght@200;300;400;600;800&family=Open+Sans:wght@400&display=swap">
<style>
  :root {
    --ink: #050505;
    --bg-deep: #0b0b0b;
    --bg-mid: #2a2a2a;
    --white: #ffffff;
    --soft-white: #e6e6e6;
    --silver: #cfcfcf;
    --band-grey: #4a4a4a;
    --ribbon: #f4f4f4;
    --ribbon-shade: #bdbdbd;
    --ribbon-text: #1a1a1a;
  }
  html, body {
    margin: 0;
    padding: 0;
    width: 776px;
    height: 1200px;
    overflow: hidden;
    background: var(--ink);
  }
  p, h1, h2 { margin: 0; }
  .flyer {
    position: relative;
    width: 776px;
    height: 1200px;
    overflow: hidden;
    font-family: "Raleway", sans-serif;
    color: var(--white);
    text-align: center;
  }
  .damask-backdrop {
    position: absolute;
    inset: 0;
    background: radial-gradient(ellipse at 50% 45%, var(--bg-mid) 0%, #161616 45%, var(--bg-deep) 100%);
  }
  .line {
    position: absolute;
    left: 0;
    width: 100%;
    margin: 0;
    white-space: nowrap;
  }
  .presenter {
    top: 66px;
    font-size: 24px;
    line-height: 30px;
    font-weight: 400;
    letter-spacing: 1.2px;
    color: var(--soft-white);
  }
  .brand-mark {
    position: absolute;
    left: 318px;
    top: 167px;
    width: 140px;
    height: 140px;
    border-radius: 50%;
    background: var(--silver);
  }
  .brand-name {
    top: 354px;
    font-size: 64px;
    line-height: 76px;
    font-weight: 300;
    letter-spacing: 14px;
    padding-left: 14px;
    box-sizing: border-box;
  }
  .brand-descriptor {
    top: 428px;
    font-size: 32px;
    line-height: 40px;
    font-weight: 400;
    letter-spacing: 8px;
    padding-left: 8px;
    box-sizing: border-box;
  }
  .tagline {
    top: 519px;
    font-size: 44px;
    font-weight: 600;
    line-height: 52px;
    letter-spacing: 1px;
  }
  .one-night-band {
    position: absolute;
    left: 175px;
    top: 632px;
    width: 427px;
    height: 46px;
    line-height: 46px;
    background: var(--band-grey);
    font-size: 28px;
    font-weight: 300;
    letter-spacing: 2px;
    color: var(--soft-white);
    white-space: nowrap;
  }
  .rule {
    position: absolute;
    height: 3px;
    background: var(--white);
  }
  .rule-top { left: 150px; width: 475px; top: 747px; }
  .rule-bottom { left: 180px; width: 425px; top: 871px; }
  .date {
    top: 765px;
    font-size: 52px;
    line-height: 60px;
  }
  .date .weekday { font-weight: 200; }
  .date .day { font-weight: 800; }
  .start-time {
    top: 823px;
    font-size: 30px;
    line-height: 36px;
    font-weight: 400;
  }
  .invite-ribbon {
    position: absolute;
    left: 176px;
    top: 902px;
    width: 424px;
    height: 72px;
  }
  .invite-label {
    position: absolute;
    left: 0;
    width: 100%;
    top: 910px;
    margin: 0;
    line-height: 52px;
    font-family: "Open Sans", sans-serif;
    font-size: 36px;
    color: var(--ribbon-text);
    white-space: nowrap;
  }
  .location-note {
    top: 1015px;
    font-size: 20px;
    line-height: 24px;
    font-weight: 400;
    letter-spacing: 4px;
    padding-left: 4px;
    box-sizing: border-box;
  }
  .host-mark {
    position: absolute;
    left: 0;
    width: 100%;
    top: 1052px;
    display: flex;
    justify-content: center;
    align-items: center;
    gap: 16px;
  }
  .host-dot {
    width: 44px;
    height: 44px;
    border-radius: 50%;
    background: var(--white);
  }
  .host-name {
    font-size: 34px;
    line-height: 44px;
    font-weight: 400;
    letter-spacing: 1px;
    white-space: nowrap;
  }
</style>
</head>
<body>
  <main class="flyer">
    <div class="damask-backdrop" role="img" aria-label="Dark black damask scroll pattern covering the background"></div>

    <p class="line presenter">VELVETROLL ATLANTA PRESENTS</p>

    <div class="brand-mark" aria-hidden="true"></div>
    <h1 class="line brand-name">LANTERN</h1>
    <p class="line brand-descriptor">NIGHTCLUB</p>

    <h2 class="line tagline">A POPUP NIGHTCLUB<br>EXPERIENCE</h2>
    <div class="one-night-band">FOR ONE NIGHT ONLY</div>

    <div class="rule rule-top"></div>
    <p class="line date"><span class="weekday">FRIDAY,</span><span class="day">OCTOBER 18</span></p>
    <p class="line start-time">PARTY BEGINS AT 9PM</p>
    <div class="rule rule-bottom"></div>

    <svg class="invite-ribbon" viewBox="0 0 424 72" aria-hidden="true">
      <polygon points="0,18 60,18 60,66 0,66 22,42" fill="var(--ribbon-shade)"/>
      <polygon points="424,18 364,18 364,66 424,66 402,42" fill="var(--ribbon-shade)"/>
      <polygon points="40,58 60,66 60,58" fill="#8a8a8a"/>
      <polygon points="384,58 364,66 364,58" fill="#8a8a8a"/>
      <rect x="40" y="8" width="344" height="52" fill="var(--ribbon)"/>
    </svg>
    <p class="invite-label">INVITE ONLY</p>

    <p class="line location-note">SEE INVITATION FOR LOCATION DETAILS</p>

    <div class="host-mark">
      <span class="host-dot" aria-hidden="true"></span>
      <span class="host-name">VELVETROLL ATLANTA</span>
    </div>
  </main>
</body>
</html>
```